Logo for a Food & Beverage Franchise Company

We need a logo and stationary for a new company that just aquired a restaurant franchise. We need a sleep and professional logo with stationary.

Target Market(s)

Adults, resturaunt owners, franchisors (Companies who own food franchise companies such as Farrowbys Head Office, Toastwell International Franchise)
and Big Food and Beverage who wish to give franchise rights to us)

Industry/Entity Type

Restaurant

Logo Text

Velvet Harbor

Logo styles of interest
Emblem Logo
Pictorial/Combination Logo
Character Logo
Font styles to use
Serif
Sans Serif

Colors
ffc214
f78f20
f37022
faa54b
fece3e
fbed22

Requirements
Must have
• Maximum three color. The less the better.
Nice to have
• It does not have to have a crown, but if you wish to have a crown then it does not have to be so sharp and clear. Abstract is better.

```html
<!DOCTYPE html>
<html lang="en">
<head>
<meta charset="UTF-8">
<title>Velvet Harbor – Business Card</title>
<link href="https://fonts.googleapis.com/css2?family=Open+Sans:wght@400;600;700&display=swap" rel="stylesheet">
<style>
  :root {
    --backdrop: #ebebeb;
    --card-dark: #3b3b3b;
    --brand-orange: #f99d1c;
    --text-light: #e6e6e6;
    --text-white: #ffffff;
    --card-shadow: rgba(0, 0, 0, 0.22);
  }
  * { margin: 0; padding: 0; box-sizing: border-box; }
  html, body {
    width: 1200px;
    height: 800px;
    overflow: hidden;
    background: var(--backdrop);
    font-family: "Open Sans", Arial, sans-serif;
  }
  .stationery {
    position: relative;
    width: 1200px;
    height: 800px;
    display: flex;
    align-items: center;
    justify-content: center;
    gap: 60px;
  }
  .card {
    position: relative;
    width: 500px;
    height: 286px;
    background: var(--card-dark);
    border-radius: 4px;
    box-shadow: 0 10px 26px var(--card-shadow);
    overflow: hidden;
  }

  /* Back of card */
  .card-back {
    display: flex;
    align-items: center;
    justify-content: center;
    gap: 14px;
  }
  .card-back .brand-square {
    width: 26px;
    height: 26px;
    background: var(--text-white);
  }
  .card-back .brand-name {
    color: var(--text-white);
    font-weight: 700;
    font-size: 30px;
    letter-spacing: 4px;
    text-transform: uppercase;
  }

  /* Front of card */
  .brand-band {
    position: absolute;
    left: 0;
    top: 0;
    width: 100%;
    height: 96px;
    background: var(--brand-orange);
    display: flex;
    flex-direction: column;
    align-items: center;
    justify-content: center;
    gap: 8px;
  }
  .brand-band .brand-square {
    width: 14px;
    height: 14px;
    background: var(--text-white);
  }
  .brand-band .brand-name {
    color: var(--text-white);
    font-weight: 600;
    font-size: 15px;
    letter-spacing: 3px;
    text-transform: uppercase;
  }
  .holder-name {
    position: absolute;
    left: 30px;
    top: 118px;
    color: var(--brand-orange);
    font-weight: 700;
    font-size: 18px;
  }
  .contact-list {
    position: absolute;
    left: 30px;
    bottom: 26px;
    list-style: none;
    color: var(--text-light);
    font-weight: 600;
    font-size: 13.5px;
    line-height: 1.4;
  }
  .contact-list .postal {
    font-size: 16px;
    font-weight: 700;
  }
</style>
</head>
<body>
  <main class="stationery">
    <section class="card card-back" aria-label="Business card back">
      <span class="brand-square"></span>
      <span class="brand-name">Velvet Harbor</span>
    </section>

    <section class="card card-front" aria-label="Business card front">
      <header class="brand-band">
        <span class="brand-square"></span>
        <span class="brand-name">Velvet Harbor</span>
      </header>
      <p class="holder-name">Samir Al Nadeem C.E.O.</p>
      <ul class="contact-list">
        <li>Office: +9714 210 4480</li>
        <li>Mobile: +97150 381 6927</li>
        <li>Email: samir@velvetharbor.com</li>
        <li class="postal">P.O. Box 5120, Dubai, UAE</li>
      </ul>
    </section>
  </main>
</body>
</html>
```